Summit Ridge Business Card

Side 1: Summit Ridge Logo (logo without Maltese cross) with industrial rope rescue related theme. Our company services - TRAINING - Fire Training, Confined Space Rescue Training, Rope Rescue training, Hazmat Training, Incident Command, EMS, Pump Operations Training. Website - summitridgeexample.com.
Side 2: Summit Ridge Fire Department Logo (logo with Maltese cross) with Firefighter related theme. Company (division) services - FIELD SERVICES - Fire Department, Stand-by Rescue, Safety, EMS, Planning. "Supporting the Emergency Response Community Since 1967"

Add contact information wherever it makes since (Name, Email, Phone).
I would like it to represent the Summit Ridge Fire Department Logo as a division not as a separate entity without saying it, possibly by depicting it in the background of Side 2 instead of being a standalone picture like the logo on Side 1.

```html
<!DOCTYPE html>
<html lang="en">
<head>
<meta charset="utf-8">
<title>Summit Ridge Business Card</title>
<link href="https://fonts.googleapis.com/css2?family=Arimo:wght@400;700&family=Montserrat:wght@800&display=swap" rel="stylesheet">
<style>
  :root {
    --backdrop: #3b3a3d;
    --card: #ffffff;
    --red: #e8301c;
    --red-edge: #f01010;
    --ink: #2e2e2e;
    --muted: #4a4a4a;
    --rule: #555555;
  }
  * { box-sizing: border-box; margin: 0; padding: 0; }
  html, body { width: 1200px; height: 779px; overflow: hidden; }
  body {
    background: var(--backdrop);
    font-family: "Arimo", Arial, sans-serif;
    color: var(--ink);
    position: relative;
  }
  .card {
    position: absolute;
    width: 540px;
    height: 310px;
    background: var(--card);
    border-radius: 22px;
    border-bottom: 6px solid var(--red-edge);
    box-shadow: 0 14px 30px rgba(0,0,0,.45);
    overflow: hidden;
  }
  /* Side 2: field services */
  .card--field { left: 40px; top: 90px; text-align: center; }
  .field__brand {
    margin-top: 70px;
    display: inline-flex;
    align-items: center;
    gap: 12px;
    font-family: "Montserrat", sans-serif;
    font-weight: 800;
    font-size: 30px;
    color: var(--red);
    letter-spacing: 1px;
  }
  .field__brand-mark { width: 18px; height: 18px; border-radius: 50%; background: var(--red); }
  .field__division {
    margin-top: 44px;
    font-family: "Montserrat", sans-serif;
    font-weight: 800;
    font-size: 20px;
    color: var(--red);
    letter-spacing: .5px;
  }
  .field__services { margin-top: 8px; font-size: 15px; color: var(--muted); }
  .field__services .dot { color: var(--red); margin: 0 4px; }
  .field__tagline { margin-top: 6px; font-size: 14px; color: var(--muted); letter-spacing: .3px; }

  /* Side 1: contact */
  .card--contact { left: 620px; top: 380px; }
  .contact__person { position: absolute; left: 34px; top: 92px; }
  .contact__name {
    font-family: "Montserrat", sans-serif;
    font-weight: 800;
    font-size: 22px;
    color: var(--red);
  }
  .contact__role { font-size: 15px; color: var(--muted); margin-top: 2px; }
  .contact__brand {
    position: absolute; right: 30px; top: 40px;
    display: flex; align-items: center; gap: 8px;
    font-family: "Montserrat", sans-serif;
    font-weight: 800;
    font-size: 22px;
    color: var(--red);
  }
  .contact__brand-mark { width: 14px; height: 14px; background: var(--red); }
  .contact__brand-rule {
    position: absolute; right: 30px; top: 76px;
    width: 190px; height: 2px; background: var(--red);
  }
  .contact__address {
    position: absolute; right: 30px; top: 100px;
    text-align: right; font-size: 14px; line-height: 1.3; color: var(--ink);
  }
  .contact__lines {
    position: absolute; left: 34px; top: 178px;
    list-style: none; font-size: 15px; line-height: 1.35;
  }
  .contact__lines li { display: flex; align-items: center; gap: 10px; }
  .contact__lines svg { width: 13px; height: 13px; flex: none; }
  .contact__rule {
    position: absolute; left: 34px; right: 30px; top: 250px;
    height: 1.5px; background: var(--rule);
  }
  .contact__training {
    position: absolute; left: 34px; right: 30px; top: 256px;
    font-size: 12.5px; line-height: 1.35; color: var(--muted);
  }
  .contact__training strong { font-weight: 400; letter-spacing: .5px; }
</style>
</head>
<body>

<section class="card card--field">
  <div class="field__brand"><span class="field__brand-mark"></span>SUMMIT RIDGE</div>
  <h2 class="field__division">FIELD SERVICES</h2>
  <p class="field__services">Fire Department<span class="dot">•</span>Stand-by Rescue<span class="dot">•</span>Safety<span class="dot">•</span>EMS<span class="dot">•</span>Planning</p>
  <p class="field__tagline">Supporting the Emergency Response Community Since 1967</p>
</section>

<section class="card card--contact">
  <div class="contact__brand"><span class="contact__brand-mark"></span>SUMMIT RIDGE</div>
  <div class="contact__brand-rule"></div>

  <div class="contact__person">
    <h1 class="contact__name">DANIEL HARPER</h1>
    <p class="contact__role">President</p>
  </div>

  <p class="contact__address">1420 Harbor Rd., Lakeview<br>TX, United States, 77000<br>www.summitridgeexample.com</p>

  <ul class="contact__lines">
    <li>
      <svg viewBox="0 0 16 16" aria-hidden="true"><path fill="#e8301c" d="M3 1l3 3-2 2c1 2 4 5 6 6l2-2 3 3-2 2C7 15 1 9 1 3z"/></svg>
      +1 555-014-0710
    </li>
    <li>
      <svg viewBox="0 0 16 16" aria-hidden="true"><rect x="4" y="1" width="8" height="14" rx="1.5" fill="none" stroke="#e8301c" stroke-width="2"/></svg>
      +1 555-014-0710
    </li>
    <li>
      <svg viewBox="0 0 16 16" aria-hidden="true"><rect x="1" y="3" width="14" height="10" fill="#e8301c"/><path d="M1 3l7 6 7-6" fill="none" stroke="#fff" stroke-width="1.5"/></svg>
      daniel@summitridgeexample.com
    </li>
  </ul>

  <div class="contact__rule"></div>
  <p class="contact__training"><strong>TRAINING</strong> - Fire Training, Confined Space Rescue Training, Rope Rescue training, Hazmat Training, Incident Command, EMS, Pump Operations Training.</p>
</section>

</body>
</html>
```